Every Shelf Set Neatly or ESN Organized needs a business card design. ESN Organized is a professi

We need a business card design that is clean, sharp and conveys a sense of organization. I already have a logo.

Target Market(s)

Families (specifically mothers), small business owners, parents, seniors

Industry/Entity Type

Business

Contact Information for Business Card

My website is www.esnorganized-example.com and my Facebook page is http://www.sociallink-example.com/everyshelfsetneatly. The phone number is 418-552-7094 and I want to be listed as Lorna M. Pelham, Owner

Requirements
Must have
• My logo.

```html
<!DOCTYPE html>
<html lang="en">
<head>
<meta charset="utf-8">
<title>Every Shelf Set Neatly – Business Card</title>
<link rel="stylesheet" href="https://fonts.googleapis.com/css2?family=Open+Sans:wght@400;600&display=swap">
<style>
  :root {
    --backdrop: #e9e7e5;
    --card-light: #f4f3f2;
    --brand-blue: #0a7bdc;
    --ink-dark: #2a2a2a;
    --ink-light: #ffffff;
  }
  * { margin: 0; padding: 0; box-sizing: border-box; }
  html, body {
    width: 1200px;
    height: 900px;
    overflow: hidden;
    background: var(--backdrop);
    font-family: "Open Sans", Arial, sans-serif;
  }
  .business-card {
    position: absolute;
    left: 160px;
    top: 178px;
    width: 880px;
    height: 545px;
    display: flex;
    box-shadow: 0 10px 30px rgba(0,0,0,0.12);
  }
  .brand-side {
    width: 429px;
    height: 100%;
    background: var(--card-light);
    display: flex;
    align-items: center;
    justify-content: center;
  }
  .brand-name {
    color: var(--brand-blue);
    font-size: 30px;
    font-weight: 400;
    letter-spacing: 2px;
    text-align: center;
    line-height: 1.3;
    margin-top: 24px;
  }
  .contact-side {
    position: relative;
    flex: 1;
    background: var(--brand-blue);
    color: var(--ink-light);
  }
  .owner-name {
    position: absolute;
    left: 24px;
    top: 98px;
    font-size: 28px;
    font-weight: 600;
    line-height: 1.2;
  }
  .owner-title {
    position: absolute;
    left: 24px;
    top: 134px;
    font-size: 22px;
    font-weight: 400;
  }
  .contact-list {
    position: absolute;
    left: 24px;
    top: 226px;
    list-style: none;
  }
  .contact-list li,
  .social-link {
    display: flex;
    align-items: center;
    font-size: 22px;
    line-height: 31px;
  }
  .contact-icon {
    width: 18px;
    height: 18px;
    margin-right: 14px;
    flex: none;
  }
  .social-link {
    position: absolute;
    left: 24px;
    top: 416px;
  }
  .social-mark {
    width: 14px;
    height: 18px;
    background: var(--ink-light);
    margin-right: 16px;
    flex: none;
  }
</style>
</head>
<body>
  <div class="business-card">
    <div class="brand-side">
      <div class="brand-name">Every Shelf Set Neatly</div>
    </div>
    <div class="contact-side">
      <div class="owner-name">Lorna M. Pelham</div>
      <div class="owner-title">Owner</div>
      <ul class="contact-list">
        <li>
          <svg class="contact-icon" viewBox="0 0 24 24" aria-hidden="true"><path fill="#fff" d="M6.6 10.8c1.4 2.8 3.8 5.1 6.6 6.6l2.2-2.2c.3-.3.7-.4 1-.2 1.1.4 2.3.6 3.6.6.6 0 1 .4 1 1V20c0 .6-.4 1-1 1C10.6 21 3 13.4 3 4c0-.6.4-1 1-1h3.5c.6 0 1 .4 1 1 0 1.3.2 2.5.6 3.6.1.3 0 .7-.2 1z"/></svg>
          418-552-7094
        </li>
        <li>
          <svg class="contact-icon" viewBox="0 0 24 24" aria-hidden="true"><rect x="3" y="6" width="18" height="12" fill="#fff"/><path d="M3 6l9 7 9-7" fill="none" stroke="#0a7bdc" stroke-width="1.6"/></svg>
          info@esnorganized-example.com
        </li>
        <li>
          <svg class="contact-icon" viewBox="0 0 24 24" aria-hidden="true"><circle cx="12" cy="12" r="9" fill="#fff"/><path d="M7 9c2 0 3 1 3 3s2 2 2 4M14 5c0 2 1 3 3 3" fill="none" stroke="#0a7bdc" stroke-width="1.6"/></svg>
          www.esnorganized-example.com
        </li>
      </ul>
      <div class="social-link">
        <span class="social-mark" aria-hidden="true"></span>
        /everyshelfsetneatly
      </div>
    </div>
  </div>
</body>
</html>
```